The Linen Loft Co

We need a business card design for our wardrobe company.
Please visit our website www.gentlelinenlofts.com to get an idea of who we are.

```html
<!DOCTYPE html>
<html lang="en">
<head>
<meta charset="utf-8">
<title>The Linen Loft Co – Business Card</title>
<link href="https://fonts.googleapis.com/css2?family=Roboto:wght@400;700&display=swap" rel="stylesheet">
<style>
  :root {
    --backdrop: #7a4424;
    --card: #ffffff;
    --ink: #111111;
    --text: #454545;
    --muted: #a3a3a3;
    --rule: #cfcfcf;
    --band-dark: #000000;
    --band-light: #9b9b9b;
  }
  * { margin: 0; padding: 0; box-sizing: border-box; }
  html, body {
    width: 1200px; height: 989px; overflow: hidden;
    background: var(--backdrop);
    font-family: "Roboto", Arial, sans-serif;
  }
  .card {
    position: absolute; left: 158px; top: 240px;
    width: 884px; height: 508px;
    background: var(--card);
    box-shadow: 0 6px 18px rgba(0,0,0,.35);
    overflow: hidden;
  }
  .brand {
    position: absolute; right: 56px; top: 70px;
    display: flex; align-items: center; gap: 16px;
  }
  .brand-mark { width: 52px; height: 52px; background: var(--ink); }
  .brand-name {
    font-weight: 700; font-size: 21px; letter-spacing: .2px;
    color: var(--ink); text-transform: uppercase;
  }
  .person { position: absolute; left: 48px; top: 280px; }
  .person-name { font-size: 34px; font-weight: 700; color: var(--ink); line-height: 40px; }
  .person-role { font-size: 23px; color: var(--muted); line-height: 26px; }
  .divider {
    position: absolute; left: 50px; top: 355px;
    width: 782px; height: 2px; background: var(--rule);
  }
  .contacts { position: absolute; left: 50px; top: 372px; list-style: none; }
  .contacts li {
    display: flex; align-items: center; gap: 12px;
    font-size: 22px; color: var(--text); height: 27px;
  }
  .contacts svg { width: 20px; height: 20px; fill: var(--ink); flex: none; }
  .address {
    position: absolute; right: 54px; top: 377px;
    text-align: right; font-size: 22px; line-height: 28px; color: var(--text);
  }
  .bands { position: absolute; left: 0; bottom: 0; width: 884px; height: 24px; }
</style>
</head>
<body>
  <section class="card">
    <div class="brand">
      <div class="brand-mark"></div>
      <div class="brand-name">The Linen Loft Co</div>
    </div>

    <div class="person">
      <div class="person-name">Daniel Hartley</div>
      <div class="person-role">President</div>
    </div>

    <div class="divider"></div>

    <ul class="contacts">
      <li>
        <svg viewBox="0 0 24 24"><path d="M6.6 10.8a15.1 15.1 0 0 0 6.6 6.6l2.2-2.2a1 1 0 0 1 1-.25 11.4 11.4 0 0 0 3.6.57 1 1 0 0 1 1 1V20a1 1 0 0 1-1 1A17 17 0 0 1 3 4a1 1 0 0 1 1-1h3.5a1 1 0 0 1 1 1c0 1.25.2 2.45.57 3.57a1 1 0 0 1-.25 1z"/></svg>
        <span>020 7946 0183</span>
      </li>
      <li>
        <svg viewBox="0 0 24 24"><path d="M2 5h20v14H2z M3.5 6.5 12 13l8.5-6.5" fill="none" stroke="#111" stroke-width="2"/><path d="M2 5h20v3l-10 7L2 8z"/></svg>
        <span>info@gentlelinenlofts.com</span>
      </li>
      <li>
        <svg viewBox="0 0 24 24"><circle cx="12" cy="12" r="10"/><path d="M7 6c2 1 1 3 3 4s1 3 0 4-1 3-2 4M15 4c-1 2 1 3 3 3s3 2 2 4-3 1-4 3 0 4 1 5" fill="none" stroke="#fff" stroke-width="1.8"/></svg>
        <span>www.gentlelinenlofts.com</span>
      </li>
    </ul>

    <address class="address" style="font-style:normal">
      Marlow House, 48 Fenwick Road<br>
      London N7 4QJ
    </address>

    <svg class="bands" viewBox="0 0 884 24" preserveAspectRatio="none">
      <polygon points="0,2 574,2 568,22 0,22" fill="var(--band-dark)"/>
      <polygon points="580,4 884,4 884,24 574,24" fill="var(--band-light)"/>
    </svg>
  </section>
</body>
</html>
```